BUSINESS CARD DESIGN

NAME- DALE VORSKIN
PHONE NUMER - 555- 714-9082
EMAIL- OFFICE@TRV-GROUNDMAKRZ.COM
BACK OF CARD- SPEACIALIZES IN LAND CLEARING, FORESTRY MUCLHING AND EXCAVATION

Contact Information for Business Card

NAME- DALE VORSKIN PHONE NUMER - 555- 714-9082 EMAIL- OFFICE@TRV-GROUNDMAKRZ.COM BACK OF CARD- SPEACIALIZES IN LAND CLEARING , MUCLHING AND EXCAVATION

```html
<!DOCTYPE html>
<html lang="en">
<head>
<meta charset="utf-8">
<title>Traverse Groundmakrz business card</title>
<link rel="stylesheet" href="https://fonts.googleapis.com/css2?family=Roboto:wght@300;400;700&family=Roboto+Condensed:wght@300;400;700&display=swap">
<style>
  :root {
    --page: #e4e8e9;
    --card: #222224;
    --card-deep: #1b1b1d;
    --pattern: #2a2a2c;
    --gold: #f9b416;
    --white: #ffffff;
  }
  * { margin: 0; padding: 0; box-sizing: border-box; }
  html, body { width: 1200px; height: 960px; overflow: hidden; background: var(--page); }
  body { position: relative; font-family: "Roboto", Arial, sans-serif; }

  .card { position: absolute; left: 247px; width: 706px; height: 404px; background: var(--card); overflow: hidden; }
  .card--front { top: 58px; }
  .card--back { top: 500px; }

  .front-texture { position: absolute; inset: 0; background: linear-gradient(180deg, var(--pattern), var(--card-deep)); }

  .brand { position: absolute; text-align: center; color: var(--gold); font-family: "Roboto", Arial, sans-serif; font-weight: 700; }
  .brand__mark { display: block; margin: 0 auto; border-radius: 50%; border: 3px solid var(--gold); }
  .brand__name { display: block; letter-spacing: 2px; line-height: 1.15; }
  .brand__phone { display: block; letter-spacing: 9px; }

  .card--front .brand { left: 0; right: 0; top: 118px; }
  .card--front .brand__mark { width: 106px; height: 106px; }
  .card--front .brand__name { margin-top: 14px; font-size: 20px; }
  .card--front .brand__phone { margin-top: 8px; font-size: 11px; }

  .tagline { position: absolute; left: 0; right: 0; top: 362px; text-align: center; color: var(--gold); font-family: "Roboto", Arial, sans-serif; font-weight: 400; font-size: 16px; letter-spacing: 0.3px; }

  .card--back .brand { left: 20px; width: 210px; top: 28px; }
  .card--back .brand__mark { width: 104px; height: 104px; }
  .card--back .brand__name { margin-top: 12px; font-size: 19px; }
  .card--back .brand__phone { margin-top: 8px; font-size: 10px; letter-spacing: 8px; }

  .holder { position: absolute; right: 36px; top: 27px; font-family: "Roboto Condensed", Arial, sans-serif; font-size: 41px; color: var(--gold); letter-spacing: 1px; line-height: 1; }
  .holder__first { font-weight: 700; }
  .holder__last { font-weight: 300; }
  .holder-tab { position: absolute; right: 0; top: 31px; width: 19px; height: 33px; background: var(--gold); }

  .contact-band { position: absolute; left: 0; top: 293px; width: 626px; height: 111px; background: var(--gold); }
  .contact-list { position: absolute; left: 24px; top: 18px; list-style: none; }
  .contact-list li { display: flex; align-items: center; height: 22.5px; color: var(--white); font-size: 15.5px; letter-spacing: 0.3px; }
  .contact-list svg { width: 15px; height: 15px; margin-right: 12px; fill: none; stroke: var(--white); stroke-width: 1.8; }

  .corner-disc { position: absolute; left: 588px; top: 296px; width: 104px; height: 104px; border-radius: 50%; background: var(--card-deep); }
</style>
</head>
<body>
  <section class="card card--front">
    <div class="front-texture" role="img" aria-label="Tiled dark embossed pattern covering the card"></div>
    <div class="brand">
      <span class="brand__mark"></span>
      <span class="brand__name">TRAVERSE GROUNDMAKRZ LLC</span>
      <span class="brand__phone">555-714-9082</span>
    </div>
    <p class="tagline">SPEACIALIZES IN LAND CLEARING , MUCLHING AND EXCAVATION</p>
  </section>

  <section class="card card--back">
    <div class="brand">
      <span class="brand__mark"></span>
      <span class="brand__name">TRAVERSE GROUNDMAKRZ LLC</span>
      <span class="brand__phone">555-714-9082</span>
    </div>

    <h1 class="holder"><span class="holder__first">DALE</span> <span class="holder__last">VORSKIN</span></h1>
    <span class="holder-tab"></span>

    <div class="contact-band">
      <ul class="contact-list">
        <li>
          <svg viewBox="0 0 16 16"><path d="M4 1.5 6 5 4.5 6.5c.8 2 2.5 3.7 4.5 4.5L10.5 9.5 14 11.5 12.5 14C7 14 2 9 2 3.5Z"/></svg>
          555- 714-9082
        </li>
        <li>
          <svg viewBox="0 0 16 16"><circle cx="8" cy="8" r="6.5"/><path d="M1.5 8h13M8 1.5c2 2 2 11 0 13M8 1.5c-2 2-2 11 0 13"/></svg>
          WWW.TRV-GROUNDMAKRZ.COM
        </li>
        <li>
          <svg viewBox="0 0 16 16"><rect x="1.5" y="3.5" width="13" height="9"/><path d="M1.5 3.5 8 9l6.5-5.5"/></svg>
          OFFICE@TRV-GROUNDMAKRZ.COM
        </li>
      </ul>
    </div>
    <span class="corner-disc"></span>
  </section>
</body>
</html>
```